Business card design for Automotive workshop

We need a business card for a new automotive repair and tyre shop called Keelstone Prime Automotive located in New Zealand. We are a clean, modern and fresh workshop and company.

Front needs to feature logo,
my name:
Marlo Fenwicke (director)

Address:
48 Tarn Lane
Whitianga 3510

Phone: 07 594 2713
Mobile: 027 451 9362
Email: office@keelstoneautomotive.example.nz
Website: keelstoneautomotive.example.nz

Back needs to feature an area to write down appointment details, date and time.

Also feature a list of jobs and work we do such as,
Vehicle Servicing
All Mechanical Repairs
Warrant of Fitness
Tyres & Wheel Alignments
Automotive Diagnostics
Automotive Parts & Supplies

```html
<!DOCTYPE html>
<html lang="en">
<head>
<meta charset="utf-8">
<title>Keelstone Prime Automotive – Business Card</title>
<link rel="stylesheet" href="https://fonts.googleapis.com/css2?family=Exo+2:ital,wght@0,300;0,400;0,600;0,700;1,400&family=Roboto:wght@400;500;700&display=swap">
<style>
  :root {
    --brand-red: #e3202a;
    --card-dark: #222222;
    --card-white: #ffffff;
    --ink: #1a1a1a;
    --ink-soft: #555555;
    --rule: #444444;
    --dots: #555555;
    --backdrop: #d9d9d9;
  }
  * { box-sizing: border-box; margin: 0; padding: 0; }
  html, body {
    width: 1200px; height: 900px; overflow: hidden;
    background: var(--backdrop);
  }
  .canvas { position: relative; width: 1200px; height: 900px; }
  .card {
    position: absolute; left: 250px; width: 700px; height: 400px;
    box-shadow: 0 6px 18px rgba(0,0,0,0.25);
    overflow: hidden;
  }

  /* ---------- Back of card ---------- */
  .card-back { top: 33px; background: var(--card-dark); }
  .card-back .brand-name {
    position: absolute; left: 46px; top: 150px;
    font-family: "Exo 2", sans-serif; font-weight: 700;
    font-size: 30px; letter-spacing: 1px; line-height: 1.1;
    color: var(--brand-red); text-transform: uppercase;
  }
  .services {
    position: absolute; left: 400px; top: 34px;
    font-family: Roboto, sans-serif; color: var(--card-white);
  }
  .services-title {
    font-weight: 700; font-size: 17px; color: var(--brand-red);
    text-transform: uppercase; margin-bottom: 5px;
  }
  .services ul { list-style: none; }
  .services li {
    font-size: 15px; font-weight: 500; line-height: 21px;
    padding-left: 18px; position: relative;
  }
  .services li::before {
    content: ""; position: absolute; left: 2px; top: 8px;
    width: 5px; height: 5px; border-radius: 50%; background: var(--brand-red);
  }
  .appointment-panel {
    position: absolute; left: 0; right: 44px; bottom: 0; height: 150px;
    background: var(--card-white);
    padding: 34px 34px 0 40px;
  }
  .appointment-row {
    display: flex; align-items: baseline; gap: 8px;
    font-family: Roboto, sans-serif; font-size: 17px; font-weight: 500;
    color: var(--brand-red); margin-bottom: 30px;
  }
  .appointment-row .fill {
    flex: 1; border-bottom: 2px dotted var(--dots); transform: translateY(-4px);
  }
  .appointment-row .fill.date { flex: 1.4; }

  /* ---------- Front of card ---------- */
  .card-front { top: 467px; background: var(--card-white); }
  .card-front .brand-name {
    position: absolute; right: 44px; top: 50px; text-align: right;
    font-family: "Exo 2", sans-serif; font-weight: 700;
    font-size: 32px; letter-spacing: 1px; line-height: 1.1;
    color: var(--brand-red); text-transform: uppercase;
  }
  .holder {
    position: absolute; left: 56px; top: 214px;
    font-family: "Exo 2", sans-serif;
  }
  .holder-name { font-size: 30px; font-weight: 700; color: var(--brand-red); line-height: 1; }
  .holder-role { font-size: 16px; font-weight: 600; color: var(--ink); margin-top: 4px; }
  .divider {
    position: absolute; left: 52px; right: 52px; top: 292px;
    border-top: 1.5px solid var(--rule);
  }
  .contacts {
    position: absolute; left: 52px; right: 30px; top: 310px;
    display: flex; justify-content: space-between; gap: 20px;
    font-family: "Exo 2", sans-serif; font-weight: 400;
    font-size: 16px; line-height: 26px; color: var(--ink-soft);
  }
  .contacts > div { flex: none; white-space: nowrap; }
  .contact-line { display: flex; align-items: center; gap: 9px; white-space: nowrap; }
  .contact-line svg { width: 14px; height: 14px; flex: none; fill: var(--brand-red); }
  .contacts .online { font-size: 14px; padding-top: 14px; }
</style>
</head>
<body>
<main class="canvas">

  <section class="card card-back" aria-label="Back of business card">
    <div class="brand-name">Keelstone Prime<br>Automotive</div>

    <div class="services">
      <h2 class="services-title">Vehicle Servicing</h2>
      <ul>
        <li>All Mechanical Repairs</li>
        <li>Warrant of Fitness</li>
        <li>Tyres &amp; Wheel Alignments</li>
        <li>Automotive Diagnostics</li>
        <li>Automotive Parts &amp; Supplies</li>
      </ul>
    </div>

    <div class="appointment-panel">
      <div class="appointment-row"><span>Date:</span><span class="fill date"></span><span>Time:</span><span class="fill"></span></div>
      <div class="appointment-row"><span>Date:</span><span class="fill date"></span><span>Time:</span><span class="fill"></span></div>
    </div>
  </section>

  <section class="card card-front" aria-label="Front of business card">
    <div class="brand-name">Keelstone Prime<br>Automotive</div>

    <div class="holder">
      <p class="holder-name">Marlo Fenwicke</p>
      <p class="holder-role">Director</p>
    </div>

    <div class="divider"></div>

    <div class="contacts">
      <div class="address">
        <p>48 Tarn Lane</p>
        <p>Whitianga 3510</p>
      </div>
      <div class="phones">
        <p class="contact-line">
          <svg viewBox="0 0 24 24" aria-hidden="true"><path d="M6.6 10.8a15.1 15.1 0 0 0 6.6 6.6l2.2-2.2c.3-.3.7-.4 1-.2 1.1.4 2.3.6 3.6.6.6 0 1 .4 1 1V20c0 .6-.4 1-1 1C10.6 21 3 13.4 3 4c0-.6.4-1 1-1h3.5c.6 0 1 .4 1 1 0 1.3.2 2.5.6 3.6.1.3 0 .7-.2 1z"/></svg>
          07 594 2713
        </p>
        <p class="contact-line">
          <svg viewBox="0 0 24 24" aria-hidden="true"><path d="M7 1h10a2 2 0 0 1 2 2v18a2 2 0 0 1-2 2H7a2 2 0 0 1-2-2V3a2 2 0 0 1 2-2zm0 3v14h10V4zm5 15.5a1 1 0 1 0 0 2 1 1 0 0 0 0-2z"/></svg>
          027 451 9362
        </p>
      </div>
      <div class="online">
        <p class="contact-line">
          <svg viewBox="0 0 24 24" aria-hidden="true"><path d="M2 5h20v14H2zm2 2v.5l8 5 8-5V7zm0 2.8V17h16V9.8l-8 5z"/></svg>
          office@keelstoneautomotive.example.nz
        </p>
        <p class="contact-line">
          <svg viewBox="0 0 24 24" aria-hidden="true"><path d="M12 2a10 10 0 1 0 0 20 10 10 0 0 0 0-20zm6.9 6h-3a15.7 15.7 0 0 0-1.4-3.6A8 8 0 0 1 18.9 8zM12 4c.8 1.2 1.5 2.5 1.9 4h-3.8c.4-1.5 1.1-2.8 1.9-4zM4.3 14a8 8 0 0 1 0-4h3.4a16 16 0 0 0 0 4zm.8 2h3a15.7 15.7 0 0 0 1.4 3.6A8 8 0 0 1 5.1 16zm3-8h-3a8 8 0 0 1 4.4-3.6C8.900 5.6 8.4 6.8 8.1 8zM12 20c-.8-1.2-1.5-2.5-1.9-4h3.8c-.4 1.5-1.1 2.8-1.9 4zm2.3-6H9.7a14.5 14.5 0 0 1 0-4h4.6a14.5 14.5 0 0 1 0 4zm.2 5.6c.6-1.2 1.1-2.4 1.4-3.6h3a8 8 0 0 1-4.4 3.6zm1.8-5.6a16 16 0 0 0 0-4h3.4a8 8 0 0 1 0 4z"/></svg>
          www.keelstoneautomotive.example.nz
        </p>
      </div>
    </div>
  </section>

</main>
</body>
</html>
```